VELMOR Website Design

We need a website designed for our company VELMOR. We are a luxury lifestyle club that will provide benefits and services for our members. The site should be clean & sleek, preferably using black and white (or darker colors). (example sites: stravenhall.example, plinth.example)

Here is a link of a sample page I did using wix. (https://dunmere7.sitehostly.example/mysite) This can be used to get a general idea.

Target Market(s)

Upper Middle Class in the United States

Number of Pages Required

5+ page

Font styles to use
Sans Serif
Other font styles liked:
• Arial (or other similar fonts)

Requirements
Must have
• A clean design that is eye-catching and speaks to our company.
Nice to have
• Ideas for copy.

```html
<!DOCTYPE html>
<html lang="en">
<head>
<meta charset="utf-8">
<title>VELMOR — A Members Only Lifestyle Club</title>
<link href="https://fonts.googleapis.com/css2?family=Raleway:wght@400;500;600;700;800&family=Lato:wght@400;700&display=swap" rel="stylesheet">
<style>
:root{
  --black:#050505;
  --ink:#1a1712;
  --gold:#e8b53c;
  --white:#ffffff;
  --muted:#d8d8d8;
  --card-text:#555555;
  --footer:#0b0b0b;
}
*{box-sizing:border-box;margin:0;padding:0}
html,body{width:1200px;height:3607px;overflow:hidden}
body{position:relative;background:var(--black);font-family:"Lato",Arial,sans-serif;color:var(--white)}
.abs{position:absolute}

/* hero */
.hero{left:0;top:0;width:1200px;height:800px}
.hero-photo{position:absolute;inset:0;clip-path:polygon(0 0,1200px 0,1200px 660px,0 795px);
  background:radial-gradient(ellipse at 50% 10%,#b0731f 0%,#6a3f16 30%,#2e1a0c 60%,#120a05 100%)}
.logo{left:132px;top:60px;font-family:"Raleway",Arial,sans-serif;font-weight:800;font-size:44px;letter-spacing:1px;color:var(--white)}
.nav{left:457px;top:75px;display:flex;gap:34px;font-family:"Raleway",Arial,sans-serif;font-weight:700;font-size:15px;letter-spacing:.3px}
.socials{left:950px;top:68px;display:flex;gap:18px}
.socials span{width:27px;height:27px;border-radius:50%;background:#2b78c8;display:block}
.hero-title{left:0;width:1200px;top:310px;text-align:center;font-family:"Raleway",Arial,sans-serif}
.hero-title .l1{font-weight:800;font-size:58px;line-height:68px}
.hero-title .l2{font-weight:400;font-size:50px;line-height:60px;letter-spacing:1px}
.btn-outline{border:2px solid var(--white);border-radius:22px;font-family:"Raleway",Arial,sans-serif;font-weight:700;color:var(--white);text-align:center}
.hero-btn{left:514px;top:461px;width:174px;height:42px;line-height:38px;font-size:15px}
.arrow{width:30px;height:30px;border-radius:50%;background:var(--black);top:371px}

/* welcome */
.welcome-title{left:137px;top:865px;font-family:"Raleway",Arial,sans-serif;font-size:42px;letter-spacing:.5px}
.welcome-title b{font-weight:800}
.welcome-sub{left:137px;top:940px;font-size:18px}
.welcome-text{left:137px;top:978px;width:505px;font-size:16px;line-height:25px;color:var(--muted)}
.read-btn{left:137px;top:1176px;width:120px;height:34px;line-height:30px;font-size:13px}
.welcome-photo{left:717px;top:866px;width:336px;height:336px;border-radius:50%;
  background:radial-gradient(circle at 50% 45%,#8b7a6a 0%,#4a3a30 45%,#1a1410 100%)}
.ring{left:703px;top:852px}

/* services */
.services{left:0;top:1323px;width:1200px;height:967px;background:var(--gold)}
.section-title{width:1200px;left:0;text-align:center;font-family:"Raleway",Arial,sans-serif;font-weight:800;font-size:40px}
.services .section-title{top:85px;color:var(--ink)}
.service{width:248px;text-align:center;color:var(--ink)}
.service.active{background:var(--ink);color:var(--white);border-radius:4px;padding-top:30px}
.service .icon{width:80px;height:80px;margin:0 auto;background:var(--ink);opacity:.85;border-radius:10px}
.service.active .icon{background:var(--white)}
.service h3{font-family:"Raleway",Arial,sans-serif;font-weight:700;font-size:24px;line-height:28px;margin-top:12px}
.service p{font-size:14px;line-height:24px;margin:12px auto 0;width:196px}

/* blog */
.blog{left:0;top:2290px;width:1200px;height:663px;background:radial-gradient(ellipse at 50% 50%,#2a2219 0%,#120e0a 70%,#070605 100%)}
.blog .section-title{top:92px}
.post{top:204px;width:291px;height:344px;background:var(--white);border-radius:3px;overflow:hidden;color:var(--card-text)}
.post .thumb{height:183px}
.post .meta{display:flex;gap:12px;padding:18px 18px 0 18px;align-items:center}
.post .cal{width:30px;height:30px;border-radius:50%;background:var(--gold);flex:none;display:flex;align-items:center;justify-content:center}
.post .date{font-size:15px;line-height:18px;color:#222}
.post p{font-size:12.5px;line-height:20px;padding:10px 18px 0 18px}

/* contact */
.contact{left:0;top:2953px;width:613px;height:474px;background:var(--gold)}
.contact-photo{left:613px;top:2953px;width:587px;height:474px;background:linear-gradient(135deg,#c9a36a 0%,#8a6a45 40%,#3d4a5a 75%,#2a3340 100%)}
.contact h2{position:absolute;left:132px;top:70px;font-family:"Raleway",Arial,sans-serif;font-weight:800;font-size:38px}
.field{position:absolute;background:var(--white);color:#666;font-size:13px;padding:10px 12px}
.submit{position:absolute;left:132px;top:354px;width:118px;height:48px;border-radius:24px;background:var(--black);color:var(--white);font-family:"Raleway",Arial,sans-serif;font-weight:800;font-size:15px;text-align:center;line-height:48px}

/* footer */
.footer{left:0;top:3427px;width:1200px;height:180px;background:var(--footer);text-align:center}
.foot-icons{position:absolute;left:0;width:1200px;top:40px;display:flex;justify-content:center;gap:8px}
.foot-icons span{width:24px;height:24px;border:1.5px solid var(--white);border-radius:50%}
.foot-links{position:absolute;left:0;width:1200px;top:90px;font-size:14px}
.copyright{position:absolute;left:0;width:1200px;top:126px;font-size:14px}
</style>
</head>
<body>

<header class="abs hero">
  <div class="hero-photo" role="img" aria-label="Guests celebrating with drinks at a nightclub under chandelier lights"></div>
  <div class="abs logo">VELMOR</div>
  <nav class="abs nav"><span>HOME</span><span>ABOUT</span><span>SERVICES &amp; BENEFITS</span><span>CONTACT</span></nav>
  <div class="abs socials"><span></span><span></span><span></span></div>
  <div class="abs arrow" style="left:100px"><svg width="30" height="30"><path d="M17 9l-6 6 6 6" fill="none" stroke="#fff" stroke-width="2.5"/></svg></div>
  <div class="abs arrow" style="left:1068px"><svg width="30" height="30"><path d="M13 9l6 6-6 6" fill="none" stroke="#fff" stroke-width="2.5"/></svg></div>
  <div class="abs hero-title"><div class="l1">A MEMBERS ONLY</div><div class="l2">LIFESTYLE CLUB</div></div>
  <div class="abs btn-outline hero-btn">GET MORE INFO</div>
</header>

<section>
  <h1 class="abs welcome-title"><b>WELCOME TO</b> VELMOR</h1>
  <div class="abs welcome-sub">The ultimate full service lifestyle club</div>
  <p class="abs welcome-text">VELMOR was formed to bring the best services, experiences, and exclusive opportunities to our members. With everything from private member events to private jet travel, the perks of being a VELMOR member are unmatched. Professional athletes, artists, musicians, corporate professionals. Our members come from diverse backgrounds.</p>
  <div class="abs btn-outline read-btn">READ MORE</div>
  <div class="abs welcome-photo" role="img" aria-label="Member posing at a party with a disco ball"></div>
  <svg class="abs ring" width="364" height="364" viewBox="0 0 364 364">
    <circle cx="182" cy="182" r="178" fill="none" stroke="var(--gold)" stroke-width="5" stroke-dasharray="250 30 250 30" transform="rotate(-80 182 182)"/>
  </svg>
</section>

<section class="abs services">
  <h2 class="abs section-title">SERVICES AND BENEFITS</h2>

  <div class="abs service" style="left:104px;top:227px">
    <div class="icon" role="img" aria-label="Calculator and ledger icon"></div>
    <h3>Accounting<br>Services</h3>
    <p>Built in the image of a Multi-Family Office VELMOR provides members with access to just about</p>
  </div>
  <div class="abs service active" style="left:349px;top:197px;height:327px">
    <div class="icon" role="img" aria-label="Investment chart icon"></div>
    <h3>Investment<br>Services</h3>
    <p>Built in the image of a Multi-Family Office VELMOR provides members with access to just about</p>
  </div>
  <div class="abs service" style="left:598px;top:227px">
    <div class="icon" role="img" aria-label="Lawyer icon"></div>
    <h3>Lawyer<br>Services</h3>
    <p>Built in the image of a Multi-Family Office VELMOR provides members with access to just about</p>
  </div>
  <div class="abs service" style="left:848px;top:227px">
    <div class="icon" role="img" aria-label="House in hand icon"></div>
    <h3>Real Estate<br>Services</h3>
    <p>Built in the image of a Multi-Family Office VELMOR provides members with access to just about</p>
  </div>

  <div class="abs service" style="left:104px;top:597px">
    <div class="icon" role="img" aria-label="Handshake clock icon"></div>
    <h3>24/7<br>Concierge</h3>
    <p>Built in the image of a Multi-Family Office VELMOR provides members with access to just about</p>
  </div>
  <div class="abs service" style="left:350px;top:597px">
    <div class="icon" role="img" aria-label="Private jet icon"></div>
    <h3>Private<br>Jet Travel</h3>
    <p>Built in the image of a Multi-Family Office VELMOR provides members with access to just about</p>
  </div>
  <div class="abs service" style="left:598px;top:597px">
    <div class="icon" role="img" aria-label="Event calendar with glass icon"></div>
    <h3>Event<br>Access</h3>
    <p>Built in the image of a Multi-Family Office VELMOR provides members with access to just about</p>
  </div>
  <div class="abs service" style="left:848px;top:597px">
    <div class="icon" role="img" aria-label="Calendar with pen icon"></div>
    <h3>Private<br>Events</h3>
    <p>Built in the image of a Multi-Family Office VELMOR provides members with access to just about</p>
  </div>
</section>

<section class="abs blog" role="region" aria-label="From the blog">
  <h2 class="abs section-title">FROM THE BLOG</h2>
  <article class="abs post" style="left:132px">
    <div class="thumb" role="img" aria-label="Friends dancing under colourful party lights" style="background:linear-gradient(135deg,#2a3a8a,#a0307a,#e0a040)"></div>
    <div class="meta"><div class="cal"><svg width="16" height="16"><rect x="2" y="3" width="12" height="11" fill="none" stroke="#fff" stroke-width="1.6"/><line x1="2" y1="7" x2="14" y2="7" stroke="#fff" stroke-width="1.6"/></svg></div><div class="date">Tuesday,<br>9 October 2018</div></div>
    <p>Sed ut perspiciatis unde omnis iste natus error sit voluptatem accusantium doloreue laudantium, totam rem aperiam, eaque ipsa quae ab illo inventore veritatis</p>
  </article>
  <article class="abs post" style="left:455px">
    <div class="thumb" role="img" aria-label="Friends toasting at a candlelit table" style="background:linear-gradient(135deg,#3a2a1a,#b07a3a,#1a120a)"></div>
    <div class="meta"><div class="cal"><svg width="16" height="16"><rect x="2" y="3" width="12" height="11" fill="none" stroke="#fff" stroke-width="1.6"/><line x1="2" y1="7" x2="14" y2="7" stroke="#fff" stroke-width="1.6"/></svg></div><div class="date">Tuesday,<br>9 October 2018</div></div>
    <p>Sed ut perspiciatis unde omnis iste natus error sit voluptatem accusantium doloreue laudantium, totam rem aperiam, eaque ipsa quae ab illo inventore veritatis</p>
  </article>
  <article class="abs post" style="left:775px">
    <div class="thumb" role="img" aria-label="Group of friends in party hats taking a photo" style="background:linear-gradient(135deg,#2a3040,#7a6a60,#c8b8a8)"></div>
    <div class="meta"><div class="cal"><svg width="16" height="16"><rect x="2" y="3" width="12" height="11" fill="none" stroke="#fff" stroke-width="1.6"/><line x1="2" y1="7" x2="14" y2="7" stroke="#fff" stroke-width="1.6"/></svg></div><div class="date">Tuesday,<br>9 October 2018</div></div>
    <p>Sed ut perspiciatis unde omnis iste natus error sit voluptatem accusantium doloreue laudantium, totam rem aperiam, eaque ipsa quae ab illo inventore veritatis</p>
  </article>
</section>

<section class="abs contact">
  <h2>GET IN TOUCH</h2>
  <div class="field" style="left:132px;top:147px;width:212px;height:38px">First Name</div>
  <div class="field" style="left:353px;top:147px;width:212px;height:38px">Last Name</div>
  <div class="field" style="left:132px;top:198px;width:212px;height:38px">Email Address</div>
  <div class="field" style="left:353px;top:198px;width:212px;height:38px">Phone Number</div>
  <div class="field" style="left:132px;top:246px;width:433px;height:78px">Message</div>
  <div class="submit">SUBMIT</div>
</section>
<div class="abs contact-photo" role="img" aria-label="Relaxed man leaning back at a desk with a laptop"></div>

<footer class="abs footer">
  <div class="foot-icons"><span></span><span></span><span></span><span></span></div>
  <div class="foot-links">Home &nbsp;/&nbsp; About &nbsp;/&nbsp; Services and Benefits &nbsp;/&nbsp; Blog &nbsp;/&nbsp; Contact</div>
  <div class="copyright">© 2018 VELMOR. All rights reserved.</div>
</footer>

</body>
</html>
```